Business Card Design Project

I need a business card designed from scratch. I have an existing logo that I can upload in Illustrator for modification or redesign.

The Company is called Query Lanterns http://querylanterns.com.au and we provide Search Engine Optimization services to Australian businesses. The current logo signifies an increase in visitors, profits etc...

There are no restrictions as to the redesign - colours, style etc are all open to change.

Cards will be full colour and one sided printed at http://www.cardmoxel.com.au so check their requirements for file format and sizes etc.

I will expect all original files upon completion of project.

Target Market(s)

Any business with a web site looking to improve their search engine rankings

Industry/Entity Type

Business

Requirements
Must have
• I like modern, sleek designs. Clean, not fussy, uncluttered.

```html
<!DOCTYPE html>
<html lang="en">
<head>
<meta charset="utf-8">
<title>Query Lanterns — Business Card</title>
<link rel="stylesheet" href="https://fonts.googleapis.com/css2?family=Nunito:wght@400;600;800&display=swap">
<style>
  :root {
    --page-bg: #e9e7e3;
    --card-bg: #f7f7f5;
    --brand-blue: #2767b0;
    --brand-yellow: #f2b51c;
    --pale-blue: #c4dcee;
    --pale-blue-soft: rgba(196, 220, 238, 0.35);
    --ink: #2a2a2a;
    --card-shadow: rgba(0, 0, 0, 0.18);
  }
  * { box-sizing: border-box; margin: 0; padding: 0; }
  html, body {
    width: 1200px;
    height: 900px;
    overflow: hidden;
    background: var(--page-bg);
    font-family: "Nunito", sans-serif;
  }
  .canvas {
    width: 1200px;
    height: 900px;
    display: flex;
    align-items: center;
    justify-content: center;
  }
  .business-card {
    position: relative;
    width: 880px;
    height: 538px;
    background: var(--card-bg);
    box-shadow: 0 10px 30px var(--card-shadow);
    padding: 56px 70px;
    color: var(--ink);
    overflow: hidden;
  }
  .brand-graphic {
    position: absolute;
    top: 0;
    right: 0;
    width: 400px;
    height: 100%;
    background: linear-gradient(135deg, var(--pale-blue) 0%, var(--pale-blue-soft) 100%);
  }
  .card-content {
    position: relative;
    z-index: 1;
  }
  .brand {
    display: flex;
    align-items: center;
    gap: 16px;
  }
  .brand-dot {
    width: 40px;
    height: 40px;
    border-radius: 50%;
    background: var(--brand-yellow);
    flex: none;
  }
  .brand-name {
    font-size: 44px;
    font-weight: 800;
    color: var(--brand-blue);
    letter-spacing: -0.5px;
    line-height: 1;
  }
  .holder {
    margin-top: 70px;
  }
  .holder-name {
    font-size: 36px;
    font-weight: 800;
    color: var(--brand-blue);
    line-height: 1.1;
  }
  .holder-role {
    font-size: 32px;
    font-weight: 400;
    color: var(--ink);
    margin-top: 4px;
  }
  .contact-list {
    list-style: none;
    margin-top: 30px;
  }
  .contact-item {
    display: flex;
    align-items: center;
    gap: 16px;
    font-size: 25px;
    line-height: 1;
    margin-bottom: 20px;
  }
  .contact-icon {
    width: 20px;
    height: 20px;
    flex: none;
    fill: var(--brand-blue);
  }
</style>
</head>
<body>
<main class="canvas">
  <article class="business-card">
    <div class="brand-graphic" role="img" aria-label="Large faint brand graphic of a rising arrow"></div>

    <div class="card-content">
      <header class="brand">
        <span class="brand-dot" aria-hidden="true"></span>
        <div class="brand-name">Query Lanterns</div>
      </header>

      <section class="holder">
        <h1 class="holder-name">Daniel Hartley</h1>
        <p class="holder-role">Director</p>
      </section>

      <ul class="contact-list">
        <li class="contact-item">
          <svg class="contact-icon" viewBox="0 0 20 20" aria-hidden="true">
            <path d="M5 2 L8 2 L9 6 L7 8 Q9 12 12 13 L14 11 L18 12 L18 15 Q18 18 15 18 Q3 17 2 5 Q2 2 5 2 Z"/>
          </svg>
          <span>1300 555 014</span>
        </li>
        <li class="contact-item">
          <svg class="contact-icon" viewBox="0 0 20 20" aria-hidden="true">
            <rect x="5" y="1" width="10" height="18" rx="2"/>
            <rect x="7" y="4" width="6" height="7" fill="#f7f7f5"/>
          </svg>
          <span>+ 61 (0)2 5550 1234</span>
        </li>
        <li class="contact-item">
          <svg class="contact-icon" viewBox="0 0 20 20" aria-hidden="true">
            <rect x="1" y="4" width="18" height="12"/>
            <path d="M1 4 L10 11 L19 4" fill="none" stroke="#f7f7f5" stroke-width="1.5"/>
          </svg>
          <span>enquiry@querylanterns.com.au</span>
        </li>
        <li class="contact-item">
          <svg class="contact-icon" viewBox="0 0 20 20" aria-hidden="true">
            <circle cx="10" cy="10" r="9"/>
            <g fill="none" stroke="#f7f7f5" stroke-width="1.2">
              <ellipse cx="10" cy="10" rx="4" ry="9"/>
              <line x1="1" y1="10" x2="19" y2="10"/>
              <line x1="10" y1="1" x2="10" y2="19"/>
            </g>
          </svg>
          <span>www.querylanterns.com.au</span>
        </li>
      </ul>
    </div>
  </article>
</main>
</body>
</html>
```